Dynamic Business Card for Sports Supplements Company

Hi! I'm looking for an awesome business card to match my existing sports supplement company. I have uploaded my current company logo and screenshot of the front page of my website.

I would like to have something dynamic and interesting and utilize the colors in the website - the reds and purples

The business card should be double sided and focus on a unique eye-catching design on the back and include all the relevant company info.

Most importantly, it should say somewhere: "Sign up on our website for a coupon code."

Target Market(s)

Mostly for women gym goers but it shouldn't be too feminine. It should be in keeping with the website design. It should flow and clearly be connected to it

Industry/Entity Type

Business

Contact Information for Business Card

Lorraine K. Vestal
CEO
LVestal@Quorvanexco.com
www.quorvanexco.com
555.417.3820
P.O. Box 47315
Alder Falls, Westmora 00000

Sign up on our website for a coupon code

Font styles to use
Serif
Sans Serif
Other font styles liked:
• Novecento font family and "Quorvanex" is in AR Destine font

Requirements
Must have
• One side should be a bold Quorvanex logo design. Even just the symbol itself may be o.k. (see attached file)

```html
<!DOCTYPE html>
<html lang="en">
<head>
<meta charset="utf-8">
<title>Quorvanex Business Card</title>
<link rel="stylesheet" href="https://fonts.googleapis.com/css2?family=Saira+Semi+Condensed:wght@700&family=Work+Sans:wght@400;500&display=swap">
<style>
  :root {
    --brand-red: #e8242a;
    --ink: #4a4a4a;
    --ink-dark: #3a3a3a;
    --paper: #ffffff;
    --backdrop: #d9d9d9;
  }
  * { box-sizing: border-box; margin: 0; padding: 0; }
  html, body { width: 1200px; height: 1000px; overflow: hidden; }
  body {
    background: var(--backdrop);
    font-family: "Work Sans", Arial, sans-serif;
    position: relative;
  }
  .card {
    position: absolute;
    left: 220px;
    width: 760px;
    height: 434px;
    box-shadow: 0 6px 18px rgba(0,0,0,0.22);
    overflow: hidden;
  }
  .card-front { top: 48px; background: var(--paper); }
  .card-back { top: 518px; background: var(--brand-red); }

  .holder { position: absolute; left: 56px; top: 56px; }
  .holder-name {
    font-family: "Saira Semi Condensed", Arial, sans-serif;
    font-weight: 700;
    font-size: 24px;
    letter-spacing: 1.5px;
    text-transform: uppercase;
    color: var(--ink-dark);
    line-height: 1;
  }
  .holder-name .accent { color: var(--brand-red); }
  .holder-title { font-size: 15px; color: var(--ink); margin-top: 4px; }

  .contact-list { position: absolute; left: 56px; top: 142px; list-style: none; }
  .contact-item {
    display: flex; align-items: center; gap: 10px;
    font-size: 17px; color: var(--ink); line-height: 26px;
  }
  .contact-item svg { width: 16px; height: 16px; flex: none; fill: var(--brand-red); }
  .contact-item .highlight { color: var(--brand-red); }

  .wordmark {
    position: absolute; right: 70px; top: 70px;
    font-family: "Saira Semi Condensed", Arial, sans-serif;
    font-weight: 700; font-size: 34px; letter-spacing: 1px;
    color: var(--brand-red); text-transform: uppercase;
  }

  .address {
    position: absolute; left: 0; right: 0; bottom: 84px;
    text-align: center; font-size: 16px; color: var(--ink);
  }
  .promo-band {
    position: absolute; left: 0; right: 0; bottom: 0; height: 60px;
    background: var(--brand-red);
    display: flex; align-items: center; justify-content: center;
  }
  .promo-band .band-square {
    position: absolute; left: 30px; top: 18px;
    width: 24px; height: 24px; background: var(--paper);
  }
  .promo-text {
    color: var(--paper); font-size: 17px; font-weight: 500;
    letter-spacing: 1.5px; text-transform: uppercase;
  }

  .back-wordmark {
    position: absolute; left: 0; right: 0; top: 0; bottom: 0;
    display: flex; flex-direction: column; align-items: center; justify-content: center; gap: 22px;
  }
  .back-wordmark .mark-square { width: 70px; height: 70px; background: var(--paper); }
  .back-wordmark .name {
    font-family: "Saira Semi Condensed", Arial, sans-serif;
    font-weight: 700; font-size: 52px; letter-spacing: 2px;
    color: var(--paper); text-transform: uppercase;
  }
</style>
</head>
<body>
  <section class="card card-front">
    <div class="holder">
      <p class="holder-name">Lorraine <span class="accent">K. Vestal</span></p>
      <p class="holder-title">CEO</p>
    </div>

    <ul class="contact-list">
      <li class="contact-item">
        <svg viewBox="0 0 16 16" aria-hidden="true"><path d="M2 5c0-2 3-3 6-3s6 1 6 3v1h-3V5H5v1H2z M4 7h8l2 6H2z M6 9h4v2H6z"/></svg>
        555.417.3820
      </li>
      <li class="contact-item">
        <svg viewBox="0 0 16 16" aria-hidden="true"><path d="M1 3h14v10H1z"/><path d="M2 4l6 5 6-5" fill="none" stroke="#fff" stroke-width="1.2"/></svg>
        LVestal@Quorvanexco.com
      </li>
      <li class="contact-item">
        <svg viewBox="0 0 16 16" aria-hidden="true"><circle cx="10" cy="6" r="4.2" fill="none" stroke="var(--brand-red)" stroke-width="2"/><path d="M7 9l-5 5" stroke="var(--brand-red)" stroke-width="2.4" stroke-linecap="round"/></svg>
        <span>www.<span class="highlight">quorvanexco</span>.com</span>
      </li>
    </ul>

    <div class="wordmark">Quorvanex</div>

    <p class="address">P.O. Box 47315 Alder Falls, Westmora 00000</p>

    <div class="promo-band">
      <span class="band-square"></span>
      <span class="promo-text">Sign up on our website for a coupon code</span>
    </div>
  </section>

  <section class="card card-back">
    <div class="back-wordmark">
      <span class="mark-square"></span>
      <span class="name">Quorvanex</span>
    </div>
  </section>
</body>
</html>
```